Create the ONLY Supplement line for Male Entrepreneurs! (Verity Nine MD)

I need a label designed for a new supplement brand that I am launching.

There are five products so need a design that I can simply change the wording for each individual product

The brand name is called verity nine MD. The focus is male entrepreneurial health.

Target audience is men 35 to 55.

Concepts: the healthier you are in body the more money you will make in business.

Concept to copy: I want to make a clean minimalistic label mimicking Lansworth MD (google it and you'll see what I mean)

Target Market(s)

male entrepreneurs 35-55

Industry/Entity Type

Health Supplement

Colors

Designer to choose colors to be used in the design.

Requirements
Must have
• Modern classy design, similar to Lansworth MD.
Nice to have
• Highlight that the supplement is Doctor Approved.
Should not have
• No loud colors. Present it as high class.

```html
<!DOCTYPE html>
<html lang="en">
<head>
<meta charset="utf-8">
<title>Verity Nine MD – Label System</title>
<link rel="stylesheet" href="https://fonts.googleapis.com/css2?family=Playfair+Display:wght@400&family=Montserrat:wght@400;500&family=Poppins:wght@400&display=swap">
<style>
  :root{
    --board:#f1f0f0;
    --paper:#ffffff;
    --plum:#450f33;
    --plum-ink:#3f0f2f;
    --plum-deep:#220d1d;
    --plum-mark:#240e1f;
    --mist:#f4f5f6;
    --rule-light:#3f0f2f;
    --rule-dark:#e6dde3;
    --edge:#6b6b6b;
    --note:#555555;
    --stage-top:#e2d4dc;
    --stage-bottom:#b7a3ad;
  }
  *{margin:0;padding:0;box-sizing:border-box}
  html,body{width:1200px;height:1050px;overflow:hidden;background:var(--board)}
  .board{position:relative;width:1200px;height:1050px;background:var(--board)}

  .label{position:absolute;overflow:hidden}
  .label--light{background:var(--paper);color:var(--plum-ink);border:1px solid var(--edge)}
  .label--dark{background:var(--plum);color:#fff}
  .label--wide{width:508px;height:323px;border-radius:4px}
  .label--tall{width:304px;height:491px;border-radius:28px}

  .label__mark-large{position:absolute;inset:0;width:100%;height:100%}
  .label--light .label__mark-large{stroke:var(--mist)}
  .label--dark .label__mark-large{stroke:var(--plum-mark)}

  .label__brand{position:absolute;font-family:"Playfair Display",serif;font-weight:400;line-height:1;white-space:nowrap;letter-spacing:-0.01em}
  .label__rule{position:absolute;height:1px}
  .label--light .label__rule{background:var(--rule-light)}
  .label--dark .label__rule{background:var(--rule-dark)}
  .label__benefit,.label__audience,.label__count{position:absolute;font-family:"Montserrat",sans-serif;font-weight:500;line-height:1;white-space:nowrap}
  .label__benefit,.label__audience{text-transform:uppercase;letter-spacing:.09em}
  .label__count{letter-spacing:.06em}
  .label__icon{position:absolute;width:44px;height:44px}
  .label--light .label__icon{stroke:var(--plum)}
  .label--dark .label__icon{stroke:#fff}

  .label__footer{position:absolute;left:0;right:0;bottom:0;display:flex;align-items:center;font-family:"Montserrat",sans-serif;font-weight:500;color:#fff;text-transform:uppercase;letter-spacing:.12em;white-space:nowrap}
  .label--light .label__footer{background:var(--plum)}
  .label--dark .label__footer{background:var(--plum-deep)}

  /* wide format */
  .label--wide .label__brand{left:19px;top:14px;font-size:61px}
  .label--wide .label__rule--brand{left:19px;top:83px;width:469px}
  .label--wide .label__benefit{left:20px;top:92px;font-size:15.5px}
  .label--wide .label__icon{left:23px;top:173px}
  .label--wide .label__audience{left:20px;top:226px;font-size:15px}
  .label--wide .label__rule--audience{left:19px;top:243px;width:242px}
  .label--wide .label__count{left:20px;top:248px;font-size:15px}
  .label--wide .label__footer{height:41px;justify-content:center;font-size:15px}

  /* tall format */
  .label--tall .label__brand{left:15px;top:255px;font-size:40px}
  .label--tall .label__rule--brand{left:16px;top:294px;width:260px}
  .label--tall .label__benefit{left:16px;top:302px;font-size:15px}
  .label--tall .label__icon{left:22px;top:342px}
  .label--tall .label__audience{left:19px;top:397px;font-size:15px}
  .label--tall .label__rule--audience{left:19px;top:415px;width:242px}
  .label--tall .label__count{left:19px;top:419px;font-size:15px}
  .label--tall .label__footer{height:42px;padding-left:16px;font-size:12.5px;letter-spacing:.1em}

  .stage{position:absolute;left:785px;top:427px;width:415px;height:623px;background:radial-gradient(ellipse at 55% 40%,var(--stage-top) 0%,var(--stage-bottom) 85%)}

  .board__note{position:absolute;left:55px;top:1011px;font-family:"Poppins",sans-serif;font-size:14px;color:var(--note);letter-spacing:.01em;white-space:nowrap}
</style>
</head>
<body>
<main class="board">

  <!-- wide, light -->
  <section class="label label--wide label--light" style="left:70px;top:62px">
    <svg class="label__mark-large" viewBox="0 0 508 323" fill="none" stroke-width="24" aria-hidden="true">
      <circle cx="365" cy="214" r="66"/>
      <line x1="412" y1="167" x2="472" y2="107"/>
      <path d="M402 104 H476 V178" stroke-linejoin="miter"/>
    </svg>
    <h1 class="label__brand">Verity Nine MD</h1>
    <div class="label__rule label__rule--brand"></div>
    <p class="label__benefit">Immunity Support</p>
    <svg class="label__icon" viewBox="0 0 44 44" fill="none" stroke-width="6" aria-hidden="true">
      <circle cx="16" cy="28" r="12"/>
      <line x1="24" y1="20" x2="38" y2="6"/>
      <path d="M25 6 H38 V19"/>
    </svg>
    <p class="label__audience">Supplement for Men</p>
    <div class="label__rule label__rule--audience"></div>
    <p class="label__count">90 softgel</p>
    <div class="label__footer">Supplement is Doctor Approved</div>
  </section>

  <!-- wide, dark -->
  <section class="label label--wide label--dark" style="left:632px;top:66px">
    <svg class="label__mark-large" viewBox="0 0 508 323" fill="none" stroke-width="24" aria-hidden="true">
      <circle cx="365" cy="214" r="66"/>
      <line x1="412" y1="167" x2="472" y2="107"/>
      <path d="M402 104 H476 V178" stroke-linejoin="miter"/>
    </svg>
    <h2 class="label__brand">Verity Nine MD</h2>
    <div class="label__rule label__rule--brand"></div>
    <p class="label__benefit">Immunity Support</p>
    <svg class="label__icon" viewBox="0 0 44 44" fill="none" stroke-width="6" aria-hidden="true">
      <circle cx="16" cy="28" r="12"/>
      <line x1="24" y1="20" x2="38" y2="6"/>
      <path d="M25 6 H38 V19"/>
    </svg>
    <p class="label__audience">Supplement for Men</p>
    <div class="label__rule label__rule--audience"></div>
    <p class="label__count">90 softgel</p>
    <div class="label__footer">Supplement is Doctor Approved</div>
  </section>

  <!-- tall, light -->
  <section class="label label--tall label--light" style="left:53px;top:493px">
    <svg class="label__mark-large" viewBox="0 0 304 491" fill="none" stroke-width="17" aria-hidden="true">
      <circle cx="208" cy="397" r="47"/>
      <line x1="242" y1="363" x2="287" y2="318"/>
      <path d="M234 317.5 H288.5 V371" stroke-linejoin="miter"/>
    </svg>
    <h2 class="label__brand">Verity Nine MD</h2>
    <div class="label__rule label__rule--brand"></div>
    <p class="label__benefit">Immunity Support</p>
    <svg class="label__icon" viewBox="0 0 44 44" fill="none" stroke-width="6" aria-hidden="true">
      <circle cx="16" cy="28" r="12"/>
      <line x1="24" y1="20" x2="38" y2="6"/>
      <path d="M25 6 H38 V19"/>
    </svg>
    <p class="label__audience">Supplement for Men</p>
    <div class="label__rule label__rule--audience"></div>
    <p class="label__count">90 softgel</p>
    <div class="label__footer">Supplement is Doctor Approved</div>
  </section>

  <!-- tall, dark -->
  <section class="label label--tall label--dark" style="left:408px;top:493px">
    <svg class="label__mark-large" viewBox="0 0 304 491" fill="none" stroke-width="17" aria-hidden="true">
      <circle cx="208" cy="397" r="47"/>
      <line x1="242" y1="363" x2="287" y2="318"/>
      <path d="M234 317.5 H288.5 V371" stroke-linejoin="miter"/>
    </svg>
    <h2 class="label__brand">Verity Nine MD</h2>
    <div class="label__rule label__rule--brand"></div>
    <p class="label__benefit">Immunity Support</p>
    <svg class="label__icon" viewBox="0 0 44 44" fill="none" stroke-width="6" aria-hidden="true">
      <circle cx="16" cy="28" r="12"/>
      <line x1="24" y1="20" x2="38" y2="6"/>
      <path d="M25 6 H38 V19"/>
    </svg>
    <p class="label__audience">Supplement for Men</p>
    <div class="label__rule label__rule--audience"></div>
    <p class="label__count">90 softgel</p>
    <div class="label__footer">Supplement is Doctor Approved</div>
  </section>

  <div class="stage" role="img" aria-label="Product bottle mock-up showing the label applied to a supplement bottle"></div>

  <p class="board__note">This mock-up is for presentation purpose only. Actual files will be aganist approved background.</p>
</main>
</body>
</html>
```